BRN website video quote promotion tiles

We are promoting vehicle leasing by video, which contains several quotation examples imported from the video. We must re-vamp the quotation tiles, contact boxes, and contact form. The first tile is generated from the video, so this must be a separate project. We are looking for a welcoming, professional flow and leave color choices to design with an emphasis on communication prompts, and additional prompts in the design would be welcome.

Target Market(s)

Any Customer interaction from the tile quotes, contact, call, message,

Industry/Entity Type

vehicle leasing

Coding

Coded - Design and coding required

Number of Pages Required

1 page

Colors

Designer to choose colors to be used in the design.

Requirements
Must have
• emphasis on point of contact and visual impact on quote tile excluding main one
Should not have
• changes to the quote structure as these imported from video pricing no changes to main image as this template which can addressed as separate project

```html
<!DOCTYPE html>
<html lang="en">
<head>
<meta charset="utf-8">
<title>BRN – Contact form and quote tiles</title>
<link href="https://fonts.googleapis.com/css2?family=Poppins:wght@400;500;600;700&display=swap" rel="stylesheet">
<style>
:root{
  --stage:#d0d0d0;
  --white:#ffffff;
  --green:#8cc04b;
  --green-light:#a6cf68;
  --green-dark:#7db343;
  --orange:#e4802f;
  --orange-tint:#fbeee4;
  --ink:#222222;
  --muted:#9a9a9a;
  --line:#dcdcdc;
  --required:#e53935;
}
*{box-sizing:border-box;margin:0;padding:0}
html,body{width:1200px;height:995px;overflow:hidden}
body{background:var(--stage);font-family:"Poppins",sans-serif;color:var(--ink);position:relative}

.page{position:absolute;left:71px;top:58px;width:1059px;height:678px;background:var(--white)}

.form-panel{position:absolute;left:126px;top:87px;width:806px;height:534px;border:1px solid var(--line);border-radius:14px;
  background:linear-gradient(155deg,#f6f6f6 0%,#fbfbfb 45%,#f6f6f6 60%,#fafafa 100%)}
.form-title{position:absolute;left:250px;top:57px;width:560px;height:54px;background:var(--white);border:1px solid var(--line);border-radius:14px;
  display:flex;align-items:center;justify-content:center;font-size:28px;font-weight:400;white-space:nowrap;line-height:1}
.form-title strong{color:var(--green);font-weight:600;margin-right:8px}

.field-label{position:absolute;font-size:12px;font-weight:400;white-space:nowrap;line-height:16px}
.field-label span{color:var(--required)}
.field-input{position:absolute;background:var(--white);border-radius:6px;box-shadow:0 1px 4px rgba(0,0,0,.08);
  font-size:12px;color:var(--muted);padding-left:20px;display:flex;align-items:center}
.field-input.textarea{align-items:flex-start;padding-top:17px}

.submit-btn{position:absolute;left:458px;top:528px;width:143px;height:45px;background:var(--green);border-radius:4px;
  color:var(--white);font-weight:600;font-size:12px;display:flex;align-items:center;justify-content:center}

.quote-tile{position:absolute;top:775px;width:268px;height:162px}
.tile-plain{left:71px;background:var(--white)}
.tile-green{left:466px;background:linear-gradient(170deg,var(--green-light),var(--green-dark));border-radius:10px;color:var(--white)}
.tile-orange{left:862px;width:267px;border:2px solid var(--orange);border-radius:12px;background:linear-gradient(180deg,#ffffff,var(--orange-tint))}

.tile-title{position:absolute;left:20px;top:16px;font-size:18px;font-weight:400;white-space:nowrap}
.tile-title strong{font-weight:600}
.tile-plain .tile-title strong{color:var(--green)}
.price{position:absolute;left:20px;top:45px;width:75px;height:20px;border-radius:10px;font-size:9px;font-weight:600;display:flex;align-items:center;justify-content:center}
.tile-plain .price{background:var(--green);color:var(--white)}
.tile-green .price{background:var(--white);color:var(--ink)}
.plus-vat{position:absolute;left:100px;top:51px;font-size:6px;font-weight:600}
.term{position:absolute;left:21px;top:72px;font-size:13px;font-weight:600;white-space:nowrap}
.tile-green .term{font-weight:500}
.includes{position:absolute;left:21px;top:90px;font-size:7.5px;white-space:nowrap}
.tile-plain .includes{color:var(--green)}
.tile-green .includes{font-weight:500}

.actions{position:absolute;left:21px;top:105px;display:flex;align-items:center}
.icon-btn{width:35px;height:35px;border-radius:50%;display:flex;align-items:center;justify-content:center}
.icon-btn svg{width:17px;height:17px}
.contact-label{font-size:11px;margin-left:7px;width:71px}

.tile-plain .call{border:2px solid var(--green)}
.tile-plain .message{background:var(--green)}
.tile-green .call{background:var(--white);box-shadow:0 0 0 3px rgba(255,255,255,.35)}
.tile-green .contact-label{font-weight:600}
.tile-green .message{border:2px solid var(--white)}
.tile-orange .call,.tile-orange .message{border:2px solid var(--orange)}

.tile-orange .tile-title{left:0;width:100%;text-align:center;top:12px}
.tile-orange .tile-title strong{color:var(--orange)}
.tile-orange .price{left:95px;top:41px;background:var(--orange);color:var(--white)}
.tile-orange .plus-vat{left:0;width:100%;text-align:center;top:65px}
.tile-orange .term{left:0;width:100%;text-align:center;top:77px}
.tile-orange .includes{left:0;width:100%;text-align:center;top:95px;color:var(--orange)}
.tile-orange .actions{left:57px;top:110px}
</style>
</head>
<body>

<section class="page">
  <div class="form-panel"></div>
  <h1 class="form-title"><strong>Please Submit your</strong> contact details</h1>

  <label class="field-label" style="left:174px;top:130px">Your name<span>*</span></label>
  <div class="field-input" style="left:175px;top:157px;width:709px;height:53px">John doe</div>

  <label class="field-label" style="left:174px;top:236px">Email address<span>*</span></label>
  <div class="field-input" style="left:175px;top:263px;width:344px;height:53px">info@johndoe.com</div>

  <label class="field-label" style="left:536px;top:236px">Phone<span>*</span></label>
  <div class="field-input" style="left:537px;top:263px;width:345px;height:53px">+1 888 888 8888</div>

  <label class="field-label" style="left:174px;top:342px">Message<span>*</span></label>
  <div class="field-input textarea" style="left:175px;top:369px;width:709px;height:138px">Your message</div>

  <div class="submit-btn">SUBMIT NOW</div>
</section>

<svg width="0" height="0" style="position:absolute">
  <defs>
    <symbol id="icon-phone" viewBox="0 0 24 24"><path d="M6.6 10.8a15.1 15.1 0 0 0 6.6 6.6l2.2-2.2c.3-.3.7-.4 1-.2 1.1.4 2.3.6 3.6.6.6 0 1 .4 1 1V20c0 .6-.4 1-1 1A17 17 0 0 1 3 4c0-.6.4-1 1-1h3.5c.6 0 1 .4 1 1 0 1.3.2 2.5.6 3.6.1.3 0 .7-.2 1z" fill="currentColor"/></symbol>
    <symbol id="icon-chat" viewBox="0 0 24 24"><path d="M4 5h16a1 1 0 0 1 1 1v10a1 1 0 0 1-1 1H9l-4 3.5V17H4a1 1 0 0 1-1-1V6a1 1 0 0 1 1-1z" fill="none" stroke="currentColor" stroke-width="1.8" stroke-linejoin="round"/><circle cx="8.5" cy="11" r="1.2" fill="currentColor"/><circle cx="12" cy="11" r="1.2" fill="currentColor"/><circle cx="15.5" cy="11" r="1.2" fill="currentColor"/></symbol>
  </defs>
</svg>

<article class="quote-tile tile-plain">
  <h2 class="tile-title"><strong>Contract</strong> Hire</h2>
  <div class="price">£ 249.27</div><div class="plus-vat">Plus VAT</div>
  <p class="term">3 Years, 9+35, 6k miles annually</p>
  <p class="includes">Complete Servicing and Maintenance included</p>
  <div class="actions">
    <span class="icon-btn call" style="color:var(--green)"><svg><use href="#icon-phone"/></svg></span>
    <span class="contact-label">Contact</span>
    <span class="icon-btn message" style="color:var(--white)"><svg><use href="#icon-chat"/></svg></span>
  </div>
</article>

<article class="quote-tile tile-green">
  <h2 class="tile-title"><strong>Contract Hire</strong></h2>
  <div class="price">£ 249.27</div><div class="plus-vat">Plus VAT</div>
  <p class="term">3 Years, 9+35, 6k miles annually</p>
  <p class="includes">Complete Servicing and Maintenance included</p>
  <div class="actions">
    <span class="icon-btn call" style="color:var(--green)"><svg><use href="#icon-phone"/></svg></span>
    <span class="contact-label">Contact</span>
    <span class="icon-btn message" style="color:var(--white)"><svg><use href="#icon-chat"/></svg></span>
  </div>
</article>

<article class="quote-tile tile-orange">
  <h2 class="tile-title"><strong>Contract</strong> Hire</h2>
  <div class="price">£ 249.27</div><div class="plus-vat">Plus VAT</div>
  <p class="term">3 Years, 9+35, 6k miles annually</p>
  <p class="includes">Complete Servicing and Maintenance included</p>
  <div class="actions">
    <span class="icon-btn call" style="color:var(--orange)"><svg><use href="#icon-phone"/></svg></span>
    <span class="contact-label">Contact</span>
    <span class="icon-btn message" style="color:var(--orange)"><svg><use href="#icon-chat"/></svg></span>
  </div>
</article>

</body>
</html>
```